VocaTerrana Community/ Talent Gallery

VocaTerrana is developing a collaborative career course, with coaching and community exchange. Goal is to offer a platform where talented candidates can show their expertise and find projects, partners, and develop their online portfolios!

Here is a good example of the type of thing we hope to create with focus on sustainability focused talent to task matching
http://www.brambleforth.com/global-themes/employment-and-growth/connecting-talent-with-opportunity-in-the-digital-age

We hope to have a "grid style" gallery where it is easy to search by talent types and focus areas within the scope of "Sustainability" issues...Food/Water/Energy, Public Health, Technology, Sustainable Cities, Infrastructure, Education, Policy, Emerging Economies, Ecosystems, Social Innovation, inclusive Security, Equity Issues. For each topic/ header we hope to have candidates post their completed portfolios to exhibit resumes, biography, a case study... they may actually prepare these on other sites, but can link in OR alternately that they can easily create here, similar to "pinqo.io" ....

Hope to include a blog space titled "Rising over the Rift", where people can mix it up across these topic issues as they are interdependent and often require partners across discipline areas! If possible another area where jobs related to these issues may be posted as project or job opportunities by potential employers.

If there is a way to create a feed from various job sites that already exist...like Jobora...or http://www.greenledgerworks.com/ that would be super great. Again...sort of a portal connection to bridge the gap ....instead of candidates having to search all the time, we are hoping they can advertise their talent and employers may search here for these well presented portfolios!

Target Market(s)

Educators, Students, Career Transitioners, Employers, Professional Associations, Talent Recruiters with focus on Sustainability related Talent to Task matching!

Industry/Entity Type

Sustainability

Number of Pages Required

4 page

Font styles to use
Sans Serif

Colors
3176b5
32b8a4
add136

Requirements
Must have
• Not sure about the coded/ uncoded option here....
• Must have - grid style area where Sustainability Professionals with varied focus areas can exhibit their talent portfolios
• appear as a Talent Gallery that starts with photos & obvious organization...other tabs to be in a menu.
• ability to search both talent and task opportunity areas to help coaches or community members make matches....some topic focused category or tag words to help make them searchable...???
• consistent professional styling to existing website and new artflock postcard shared in brief/ images area
• Interactive blog space where articles, issues may be posted, discussed
• Bulletin board or feed for project opportunities to be posted where candidates may locate them and/or employers may express specific "call" for talent..These may be Short term Internships, Projects, Consulting Team Opportunity, or Jobs/ part time to full time....
Nice to have
• A calendar area where we can post networking opportunities, issues presentations where potential partners can meet the next generation leaders, attend a forum or webinar presentation.
Should not have
• Too much text on front page...Should be clean design,

```html
<!DOCTYPE html>
<html lang="en">
<head>
<meta charset="utf-8">
<title>VocaTerrana – Collaborative Career Course</title>
<link href="https://fonts.googleapis.com/css2?family=Open+Sans:wght@400;600;700&family=Montserrat:wght@600;700&display=swap" rel="stylesheet">
<style>
:root{
  --blue:#3176b5;
  --blue-dark:#2a66a0;
  --teal:#32b8a4;
  --teal-dark:#1f8f80;
  --green:#add136;
  --navy:#0e2039;
  --ink:#2b3440;
  --muted:#6b7480;
  --line:#e3e7ea;
  --white:#ffffff;
}
*{box-sizing:border-box;margin:0;padding:0}
html,body{width:1200px;height:3884px;overflow:hidden}
body{font-family:"Open Sans",Arial,sans-serif;color:var(--ink);background:var(--white);font-size:14px;line-height:1.55}
h1,h2,h3,h4{font-family:"Montserrat","Open Sans",sans-serif}
.wrap{width:1000px;margin:0 auto;position:relative}

/* header */
.site-header{height:140px;background:var(--white);position:relative}
.topbar{position:absolute;right:100px;top:10px;display:flex;gap:24px;align-items:center;font-size:12px;color:var(--muted)}
.topbar .dot{display:inline-block;width:10px;height:10px;border-radius:50%;background:var(--teal);margin-right:6px;vertical-align:-1px}
.btn-login{background:var(--green);color:var(--navy);font-weight:700;padding:6px 20px;border-radius:3px;font-size:13px}
.brand{position:absolute;left:100px;top:22px;display:flex;align-items:center;gap:14px}
.brand-mark{width:84px;height:84px;border-radius:50%;background:var(--blue)}
.brand-name{font-weight:700;font-size:26px;color:var(--blue)}
.main-nav{position:absolute;right:100px;top:62px;display:flex;gap:30px;font-size:15px;font-weight:600;color:var(--ink)}
.main-nav .home{background:var(--teal);color:#fff;padding:2px 14px;border-radius:3px}

/* hero */
.hero{height:640px;position:relative;background:linear-gradient(180deg,#8aa7b5 0%,#b99a7e 40%,#6a4a33 75%,#3f2d22 100%);display:flex;flex-direction:column;align-items:center;justify-content:flex-end;padding-bottom:80px}
.hero .photo{position:absolute;inset:0}
.hero h1{position:relative;color:#fff;font-size:36px;line-height:1.3;text-align:center;text-shadow:0 2px 6px rgba(0,0,0,.45)}
.btn-start{position:relative;margin-top:24px;background:var(--green);color:var(--navy);font-weight:700;font-size:16px;padding:10px 30px;border-radius:4px}
.hero .arrow{position:absolute;top:300px;width:30px;height:30px;border-radius:50%;background:rgba(255,255,255,.35)}
.hero .arrow.l{left:30px}.hero .arrow.r{right:30px}

.divider{height:0;position:relative;z-index:2}
.divider span{position:absolute;left:50%;top:-32px;margin-left:-32px;width:64px;height:64px;border-radius:50%;background:var(--white);border:8px solid var(--teal)}

/* mission */
.mission{height:310px;padding-top:60px}
.mission .wrap{display:flex;justify-content:space-between}
.mission-text{width:560px}
.section-title{font-size:40px;font-weight:700;color:var(--navy)}
.section-title em{font-style:normal;color:var(--teal)}
.mission-text p{font-size:12px;color:var(--muted);margin:16px 0 14px}
.btn-read{display:inline-block;background:var(--teal);color:#fff;font-weight:700;font-size:13px;padding:6px 22px;border-radius:3px}
.mission-photo{width:330px;height:190px;background:linear-gradient(135deg,#c9d3df,#5c7fa8);margin-top:-20px}

/* services */
.services{height:490px;background:var(--blue);color:#fff;padding-top:48px;position:relative}
.services h2{text-align:center;font-size:34px}
.services-body{position:relative;width:1000px;height:360px;margin:30px auto 0}
.services-wheel{position:absolute;left:365px;top:20px;width:270px;height:270px;border-radius:50%;background:radial-gradient(circle,#2a9f8e 0%,var(--teal) 35%,var(--green) 70%,#2f5f98 100%)}
.service{position:absolute;width:240px;font-size:11px}
.service h3{font-size:15px;margin-bottom:4px}
.service .icon{width:46px;height:46px;border-radius:50%;border:3px solid #fff;margin-bottom:8px}
.service.left{text-align:right}
.service.left .icon{margin-left:auto}
.s1{left:90px;top:10px}.s2{right:90px;top:10px}.s3{left:90px;top:180px}.s4{right:90px;top:180px}
.service p{opacity:.85}

/* four phase */
.phases{height:680px;padding-top:70px;text-align:center}
.phases .intro{width:720px;margin:18px auto 16px;font-size:12px;color:var(--muted)}
.phase-grid{display:grid;grid-template-columns:repeat(4,1fr);gap:20px;margin-top:50px}
.phase-card{text-align:center}
.phase-card .photo{height:200px;background:linear-gradient(135deg,#d8dee6,#7d8fa5)}
.phase-card h4{margin-top:30px;font-size:18px;color:var(--navy);letter-spacing:1px}
.phase-card p{font-size:11px;color:var(--muted)}
.phase-card .bar{height:6px;background:var(--teal);margin-top:10px}

/* gallery */
.gallery{height:630px;background:var(--teal);padding-top:40px}
.gallery h2{text-align:center;color:#fff;font-size:34px}
.gallery-grid{display:grid;grid-template-columns:230px 230px 180px 180px 130px;grid-template-rows:200px 200px;gap:10px;margin-top:40px}
.tile{position:relative;background:linear-gradient(160deg,#9bb0c0,#3f5a6f)}
.tile .label{position:absolute;left:0;right:0;bottom:0;background:rgba(14,32,57,.82);color:#fff;font-size:13px;font-weight:600;padding:6px 10px}
.tile.infra{grid-row:1/3;background:linear-gradient(180deg,#e0a25a,#6b4a2e)}
.tile.food{background:linear-gradient(160deg,#b4d28a,#3d6d3a)}
.tile.cities{background:linear-gradient(160deg,#8fb4d0,#3b6a4a)}
.tile.edu{grid-column:4/6;background:linear-gradient(160deg,#c7cdd6,#5a6a80)}
.tile.health{background:linear-gradient(160deg,#8b96a6,#34404f)}
.tile.tech{grid-column:3/5;background:linear-gradient(160deg,#3c7bc7,#122d5a)}
.tile.more{background:var(--navy);display:flex;align-items:center;justify-content:center;color:#fff;font-weight:700;font-size:16px;text-align:center}

/* blog */
.blog{height:530px;padding-top:70px}
.blog h2{text-align:center}
.blog-grid{display:grid;grid-template-columns:repeat(3,1fr);gap:60px;margin-top:50px}
.post .photo{position:relative;height:170px;background:linear-gradient(135deg,#8ba0b4,#3d4c5e)}
.post .photo.warm{background:linear-gradient(135deg,#e7b05a,#9a3b1e)}
.post .photo.dark{background:linear-gradient(135deg,#7a6a55,#2e2a24)}
.date{position:absolute;left:0;top:0;width:52px;background:var(--teal);color:#fff;text-align:center;font-weight:700;line-height:1.1;padding:6px 0}
.date b{display:block;font-size:20px}
.date small{font-size:11px}
.post h4{font-size:15px;color:var(--navy);margin:12px 0 6px}
.post p{font-size:12px;color:var(--muted);margin-bottom:10px}
.post .btn-read{font-size:11px;padding:4px 14px}

/* footer */
.site-footer{height:464px;background:var(--navy);color:#cfd8e3;position:relative;padding-top:60px}
.site-footer .divider span{top:-92px;border-color:var(--teal);background:var(--navy)}
.footer-nav{display:flex;justify-content:center;gap:40px;font-size:14px;font-weight:600;color:#fff;padding-bottom:30px;border-bottom:1px solid rgba(255,255,255,.12)}
.footer-cols{display:grid;grid-template-columns:1fr 1fr 1fr;gap:60px;margin-top:36px}
.footer-cols h4{color:var(--teal);font-size:18px;margin-bottom:16px}
.contact li{list-style:none;font-size:12px;margin-bottom:12px;display:flex;gap:10px}
.contact i{width:12px;height:12px;border-radius:50%;background:var(--teal);flex:none;margin-top:3px}
.field{height:26px;background:#fff;border-radius:2px;margin-bottom:8px;font-size:11px;color:#8a94a0;padding:4px 8px}
.field.tall{height:46px}
.btn-submit{display:inline-block;background:var(--teal);color:#fff;font-weight:700;font-size:12px;padding:5px 20px;border-radius:3px}
.feeds p{font-size:12px;margin-bottom:6px}
.feeds p.title{color:#fff;font-weight:600}
.feeds p.sub{color:var(--green);font-size:11px}
.footer-bottom{position:absolute;left:100px;right:100px;bottom:24px;display:flex;justify-content:space-between;align-items:center;font-size:11px}
.social{display:flex;gap:8px}
.social span{width:22px;height:22px;border-radius:50%;background:var(--blue)}
</style>
</head>
<body>

<header class="site-header">
  <div class="brand"><span class="brand-mark"></span><span class="brand-name">VocaTerrana</span></div>
  <div class="topbar">
    <span><span class="dot"></span>555-018-2247</span>
    <span><span class="dot"></span>info@vocaterrana.com</span>
    <span class="btn-login">Log In</span>
  </div>
  <nav class="main-nav"><span class="home">Home</span><span>About Us</span><span>Services</span><span>Blog</span><span>Contact Us</span></nav>
</header>

<section class="hero">
  <div class="photo" role="img" aria-label="Cupped hands holding soil with a young green seedling"></div>
  <span class="arrow l"></span><span class="arrow r"></span>
  <h1>We Are Developing A Collaborative Career Course<br>With Coaching And Community Exchange</h1>
  <span class="btn-start">Get Start Now</span>
</section>

<div class="divider"><span></span></div>

<section class="mission">
  <div class="wrap">
    <div class="mission-text">
      <h2 class="section-title">Our <em>Mission</em> &amp; Philosophy</h2>
      <p>Our mission is to cultivate a community of learning and professional practice to support career transitions and next generation leadership of sustainable solutions that balance economic, environmental and equity needs. We match talent to task across disciplines, guided by coaching, mentoring and shared experience, so that emerging professionals can grow portfolios, build partnerships and deliver change where it is needed most.</p>
      <span class="btn-read">Read More</span>
    </div>
    <div class="mission-photo" role="img" aria-label="Hands joining colourful puzzle pieces in a circle"></div>
  </div>
</section>

<section class="services">
  <h2>Our Services</h2>
  <div class="services-body">
    <div class="services-wheel" role="img" aria-label="Circular diagram of four interlocking service areas"></div>
    <div class="service left s1"><div class="icon"></div><h3>Next Generation Talent</h3><p>Showcase skills and portfolios to partners seeking sustainability talent.</p></div>
    <div class="service s2"><div class="icon"></div><h3>Online Coaching</h3><p>Flexible guidance sessions to shape goals and plan career transitions.</p></div>
    <div class="service left s3"><div class="icon"></div><h3>Courses</h3><p>Structured modules on leadership, collaboration and sustainable practice.</p></div>
    <div class="service s4"><div class="icon"></div><h3>In Person Coaching</h3><p>Small group meetings that connect learners with experienced mentors.</p></div>
  </div>
</section>

<section class="phases">
  <div class="wrap">
    <h2 class="section-title">Four <em>Phase</em> Career Course</h2>
    <p class="intro">Through a proven four phase process integrating principles of lifelong learning, career transitions, entrepreneurship and innovation, our interdisciplinary collaborative course is designed to guide you through creative change for career lifestyle and next generation leadership.</p>
    <span class="btn-read">Read More</span>
    <div class="phase-grid">
      <div class="phase-card"><div class="photo" role="img" aria-label="Team fitting puzzle pieces together"></div><h4>CLARIFY</h4><p>Personal Profile, Vision &amp; Mission</p><div class="bar"></div></div>
      <div class="phase-card"><div class="photo" role="img" aria-label="Colleagues talking around a table"></div><h4>COMMUNICATE</h4><p>Personal Profile, Vision &amp; Mission</p><div class="bar"></div></div>
      <div class="phase-card"><div class="photo" role="img" aria-label="Group stacking hands in teamwork"></div><h4>COLLABORATE</h4><p>Personal Profile, Vision &amp; Mission</p><div class="bar"></div></div>
      <div class="phase-card"><div class="photo" role="img" aria-label="Professional looking over a city skyline"></div><h4>CREATE</h4><p>Personal Profile, Vision &amp; Mission</p><div class="bar"></div></div>
    </div>
  </div>
</section>

<section class="gallery">
  <div class="wrap">
    <h2>Our Gallery</h2>
    <div class="gallery-grid">
      <div class="tile infra" role="img" aria-label="Construction cranes at sunset"><span class="label">Infrastructure</span></div>
      <div class="tile food" role="img" aria-label="Seedling growing from soil"><span class="label">Food/Water/Energy</span></div>
      <div class="tile cities" role="img" aria-label="Green city skyline"><span class="label">Sustainable Cities</span></div>
      <div class="tile edu" role="img" aria-label="Students in a classroom"><span class="label">Education</span></div>
      <div class="tile health" role="img" aria-label="Public health lettering on a wall"><span class="label">Public Health</span></div>
      <div class="tile tech" role="img" aria-label="Digital technology network"><span class="label">Technology</span></div>
      <div class="tile more">View<br>More</div>
    </div>
  </div>
</section>

<section class="blog">
  <div class="wrap">
    <h2 class="section-title">Rising <em>Over</em> The Rift</h2>
    <div class="blog-grid">
      <article class="post"><div class="photo" role="img" aria-label="People in a workshop discussion"><span class="date"><b>23</b><small>JUN</small></span></div><h4>Ecosystem Insights for Leaders</h4><p>An offering for leaders engaged in systems change, where shared practice meets nature-based thinking.</p><span class="btn-read">Read More</span></article>
      <article class="post"><div class="photo dark" role="img" aria-label="Book cover on sustainable development"><span class="date"><b>23</b><small>JUN</small></span></div><h4>Sustainable Development</h4><p>A new edition of a key text explores the age of sustainable development and its practical paths.</p><span class="btn-read">Read More</span></article>
      <article class="post"><div class="photo warm" role="img" aria-label="Plate of grilled food"><span class="date"><b>23</b><small>JUN</small></span></div><h4>Food Security</h4><p>We may not all share the same ideas, but we all depend on what arrives on the table each day.</p><span class="btn-read">Read More</span></article>
    </div>
  </div>
</section>

<footer class="site-footer">
  <div class="divider"><span></span></div>
  <div class="wrap">
    <nav class="footer-nav"><span>Home</span><span>About Us</span><span>Services</span><span>Blog</span><span>Contact Us</span></nav>
    <div class="footer-cols">
      <div>
        <h4>Contact Details</h4>
        <ul class="contact">
          <li><i></i>1420 Fernhollow Lane, Marlow Bay</li>
          <li><i></i>555-018-2247</li>
          <li><i></i>555-018-2248</li>
          <li><i></i>info@vocaterrana.com</li>
        </ul>
      </div>
      <div>
        <h4>Quick Inquiry</h4>
        <div class="field">Name</div>
        <div class="field">Email</div>
        <div class="field tall">Message</div>
        <span class="btn-submit">Submit</span>
      </div>
      <div class="feeds">
        <h4>View Feeds</h4>
        <p class="title">VERDANT PATH ROLES</p>
        <p>Education Development Coordinator</p>
        <p class="sub">Urban Growth Council</p>
        <p>Environmental Communications Specialist</p>
        <p class="sub">Coastal Research Group</p>
        <p>Sales Coordinator</p>
        <p class="sub">Renewables Co-op</p>
      </div>
    </div>
  </div>
  <div class="footer-bottom">
    <span>© 2016 VocaTerrana. All Rights Reserved.</span>
    <span class="social"><span></span><span></span><span></span><span></span><span></span></span>
  </div>
</footer>

</body>
</html>
```